I need a label design to go on our jars of honey. Our company is called Marrowdale Honey Co. The type of honey is called Fernlight Glen Honey. The jars are 1kg. Attached is the label size. Left hand side needs to have nutritional info... as attached. Middle section is our company name, honey type, 1kg & Tuiwhenua Bay, NZ. Right hand side needs to have info as per photo (raw honey etc). I would like to upload more pictures... but I’m unsure how to do this? Thanks, Carla

Target Market(s)

Honey consumers... families

Industry/Entity Type

Food Production

Colors

Designer to choose colors to be used in the design.

Requirements
Must have
• Nutritional info as per upload
• Type of honey & company name as per upload
• 1kg
• Address
Nice to have
• Similar fonts to upload.
• Possibly background image... floral or beach... very faint though.

```html
<!DOCTYPE html>
<html lang="en">
<head>
<meta charset="utf-8">
<title>Marrowdale Honey Co. – Fernlight Glen Honey label</title>
<link rel="stylesheet" href="https://fonts.googleapis.com/css2?family=Josefin+Sans:wght@300;400&family=Pacifico&family=Patrick+Hand&family=Source+Sans+3:wght@400;600&display=swap">
<style>
  :root {
    --copper-light: #c98f6c;
    --copper-mid: #b57655;
    --copper-dark: #9c5e42;
    --cream: #fffaf4;
    --bloom-pink: #e0468f;
    --bloom-orange: #f08a4b;
    --bloom-purple: #9b4fb0;
    --leaf-teal: #5cc3a4;
  }
  * { box-sizing: border-box; margin: 0; padding: 0; }
  html, body { width: 1200px; height: 604px; overflow: hidden; background: #ffffff; }
  .label {
    position: relative;
    width: 1200px;
    height: 604px;
    overflow: hidden;
    color: var(--cream);
    background:
      radial-gradient(ellipse 55% 70% at 50% 45%, var(--copper-light) 0%, var(--copper-mid) 60%, var(--copper-dark) 100%);
  }

  /* Flower clusters */
  .bloom { position: absolute; }
  .bloom--top { left: 712px; top: 0; width: 270px; height: 222px; }
  .bloom--bottom { left: 280px; top: 322px; width: 200px; height: 282px; }

  /* Left panel */
  .panel-left {
    position: absolute; left: 42px; top: 12px; width: 250px;
    font-family: "Source Sans 3", sans-serif; text-align: center;
  }
  .origin { font-size: 15px; line-height: 19px; }
  .nutrition {
    position: absolute; left: 2px; top: 97px; width: 248px; height: 200px;
    border: 1.5px solid var(--cream); font-size: 11.5px; text-align: left;
  }
  .nutrition__title {
    font-weight: 400; font-size: 14px; line-height: 20px; padding: 1px 6px 1px;
    border-bottom: 1.5px solid var(--cream);
  }
  .nutrition__servings { padding: 4px 6px 5px; border-bottom: 1.5px solid var(--cream); line-height: 16px; font-weight: 600; font-size: 12px; }
  .nutrition table { width: 100%; border-collapse: collapse; }
  .nutrition th { font-weight: 400; font-size: 10px; line-height: 14px; padding: 2px 6px; border-bottom: 1px solid var(--cream); text-align: left; }
  .nutrition td { padding: 0 6px; line-height: 14.5px; font-weight: 600; }
  .nutrition td + td, .nutrition th + th { padding-left: 2px; }
  .nutrition tr:first-child td { padding-top: 4px; }
  .storage { position: absolute; left: 0; top: 322px; width: 254px; font-size: 16px; line-height: 22px; }
  .batch {
    position: absolute; left: 2px; top: 468px; width: 248px; height: 82px;
    border: 1.5px solid var(--cream);
    text-align: left; font-size: 15px; line-height: 19px; padding: 5px 8px;
  }

  /* Centre panel */
  .panel-centre { position: absolute; left: 400px; top: 0; width: 400px; height: 604px; text-align: center; }
  .brand { position: absolute; top: 64px; left: 0; width: 400px; font-family: "Josefin Sans", sans-serif; font-weight: 400; color: var(--cream); }
  .brand__name { display: block; font-size: 42px; line-height: 46px; letter-spacing: 0.5px; }
  .brand__sub { display: block; font-family: "Josefin Sans", sans-serif; font-weight: 300; font-size: 23px; line-height: 30px; letter-spacing: 3px; }
  .product {
    position: absolute; top: 238px; left: 0; width: 400px;
    font-family: "Pacifico", cursive; font-weight: 400;
    font-size: 52px; line-height: 56px; color: var(--cream);
  }
  .weight { position: absolute; top: 456px; left: 0; width: 400px; font-family: "Patrick Hand", cursive; font-size: 52px; line-height: 52px; }
  .place { position: absolute; top: 518px; left: 0; width: 400px; font-family: "Patrick Hand", cursive; font-size: 36px; line-height: 40px; }

  /* Right panel */
  .panel-right {
    position: absolute; left: 890px; top: 72px; width: 300px;
    font-family: "Patrick Hand", cursive; font-size: 18.5px; line-height: 22px; text-align: center;
  }
  .panel-right p + p { margin-top: 22px; }
  .panel-right .thanks { margin-top: 79px; }
  .panel-right .contact { margin-top: 55px; }
</style>
</head>
<body>
<main class="label">

  <svg class="bloom bloom--top" viewBox="0 0 270 222" role="img" aria-label="Cluster of hibiscus flowers and leaves">
    <defs>
      <radialGradient id="bloomTop" cx="50%" cy="45%" r="55%">
        <stop offset="0%" stop-color="#f08a4b"/>
        <stop offset="45%" stop-color="#e0468f"/>
        <stop offset="80%" stop-color="#9b4fb0" stop-opacity="0.7"/>
        <stop offset="100%" stop-color="#5cc3a4" stop-opacity="0"/>
      </radialGradient>
    </defs>
    <ellipse cx="140" cy="95" rx="132" ry="118" fill="url(#bloomTop)"/>
  </svg>

  <svg class="bloom bloom--bottom" viewBox="0 0 200 282" role="img" aria-label="Cluster of hibiscus flowers and leaves">
    <defs>
      <radialGradient id="bloomBottom" cx="50%" cy="55%" r="55%">
        <stop offset="0%" stop-color="#f08a4b"/>
        <stop offset="45%" stop-color="#e0468f"/>
        <stop offset="80%" stop-color="#9b4fb0" stop-opacity="0.7"/>
        <stop offset="100%" stop-color="#5cc3a4" stop-opacity="0"/>
      </radialGradient>
    </defs>
    <ellipse cx="100" cy="150" rx="100" ry="132" fill="url(#bloomBottom)"/>
  </svg>

  <section class="panel-left">
    <p class="origin">100% New Zealand Honey<br>No added ingredients</p>
    <div class="nutrition">
      <h2 class="nutrition__title">NUTRITIONAL INFORMATION</h2>
      <p class="nutrition__servings">Servings per package: 100<br>Serving size: 10g</p>
      <table>
        <thead>
          <tr><th>Average Quantity</th><th>per Serving</th><th>per 100g</th></tr>
        </thead>
        <tbody>
          <tr><td>Energy</td><td>134kj</td><td>1340kj</td></tr>
          <tr><td>Protein</td><td>0.04g</td><td>0.4g</td></tr>
          <tr><td>Fat total</td><td>0g</td><td>0g</td></tr>
          <tr><td>&nbsp;- saturated</td><td>0g</td><td>0g</td></tr>
          <tr><td>Carbohydrate</td><td>7.9g</td><td>79g</td></tr>
          <tr><td>&nbsp;- sugars</td><td>7.8g</td><td>78.1g</td></tr>
          <tr><td>Sodium</td><td>1.2mg</td><td>12mg</td></tr>
        </tbody>
      </table>
    </div>
    <p class="storage">Store upright in a cool, dry place.<br>No refrigeration needed.<br>Not recomended for infants<br>below the age of 12 months.</p>
    <div class="batch">Best before:<br>RMP:<br>Batch No:</div>
  </section>

  <section class="panel-centre">
    <h1 class="brand">
      <span class="brand__name">MARROWDALE</span>
      <span class="brand__sub">HONEY CO.</span>
    </h1>
    <h2 class="product">Fernlight<br>Glen Honey</h2>
    <p class="weight">1kg</p>
    <p class="place">Tuiwhenua Bay, NZ</p>
  </section>

  <section class="panel-right">
    <p>Sourced from the beautiful<br>Kōwhai Peninsula.</p>
    <p>Our honey comes to you raw &amp;<br>unpasteurised, ensured it retains<br>all the natural goodness!</p>
    <p>Arohanui,<br>Rowan, Carla &amp; boys</p>
    <p class="thanks">'Marrowdale' - all thanks to God for<br>His incredible creation!</p>
    <p class="contact">www.marrowdalehoney.co.nz<br>42 Kereru Lane<br>Tuiwhenua Bay<br>New Zeland</p>
  </section>

</main>
</body>
</html>
```